Request for Business Card Design

Hi. My name is Marlene, I am looking for a new business card design for my company, Quarrow Signal Instruments, LLC. I really like the design you did for Tarsel Venture and was hoping you could do something similar using our full logo and our mark. I am also open to any raised texture design using our mark. I have attached our full logo, which would need to be somewhere on the card, as well as the mark in both outline and full form, as well as our brand colors / guide. The card does not have to be white, as long as our logo and mark appear. I actually like darker colored business cards more, but am open to all options. If you are interested in working with me, please let me know. We would also take the business card design into letterhead design if you can do that.

```html
<!DOCTYPE html>
<html lang="en">
<head>
<meta charset="utf-8">
<title>Quarrow Signal Instruments — Business Card</title>
<link rel="stylesheet" href="https://fonts.googleapis.com/css2?family=Open+Sans:wght@400;600;700&display=swap">
<style>
  :root {
    --backdrop: #222223;
    --card: #3b3b3d;
    --card-edge: #2c2c2e;
    --brand-blue: #1a95bf;
    --ink-light: #f2f2f2;
    --ink-soft: #d9d9db;
    --emboss: #1f1f21;
  }
  * { box-sizing: border-box; margin: 0; padding: 0; }
  html, body {
    width: 1200px; height: 780px; overflow: hidden;
    background: var(--backdrop);
    font-family: "Open Sans", Arial, sans-serif;
  }
  .canvas {
    position: relative; width: 1200px; height: 780px;
    display: flex; align-items: center; justify-content: center; gap: 50px;
  }
  .card {
    position: relative; width: 540px; height: 310px;
    background: var(--card);
    box-shadow: 0 3px 0 var(--card-edge), 0 6px 0 #262628, 0 18px 40px rgba(0,0,0,.45);
  }

  /* Front side */
  .contact {
    position: absolute; left: 34px; top: 104px;
    color: var(--ink-light); font-size: 13.5px; line-height: 1.45;
  }
  .contact__address { margin-bottom: 6px; margin-left: 24px; }
  .contact__list { list-style: none; }
  .contact__item { display: flex; align-items: center; gap: 9px; }
  .contact__icon { width: 14px; height: 14px; flex: none; fill: var(--brand-blue); }

  .brand {
    position: absolute; right: 38px; top: 70px;
    display: flex; align-items: center; gap: 12px;
  }
  .brand__dot {
    width: 34px; height: 34px; border-radius: 50%;
    background: var(--brand-blue); flex: none;
  }
  .brand__name {
    color: var(--ink-light); font-weight: 700;
    font-size: 19px; line-height: 1.15; letter-spacing: .04em; text-transform: uppercase;
  }

  .person {
    position: absolute; right: 40px; bottom: 26px; text-align: right;
  }
  .person__name {
    color: var(--brand-blue); font-weight: 600; font-size: 34px; line-height: 1;
  }
  .person__role {
    color: var(--ink-light); font-size: 16px; margin-top: 4px;
  }

  /* Back side */
  .card--back { display: flex; align-items: center; justify-content: center; }
  .brand--raised { position: static; gap: 18px; }
  .brand--raised .brand__dot { width: 58px; height: 58px; background: var(--emboss); }
  .brand--raised .brand__name { color: var(--emboss); font-size: 30px; }
</style>
</head>
<body>
<main class="canvas">

  <section class="card card--front" aria-label="Business card front">
    <div class="contact">
      <p class="contact__address">1180 Millbrook Park Drive,<br>Alder Falls, CO 80611</p>
      <ul class="contact__list">
        <li class="contact__item">
          <svg class="contact__icon" viewBox="0 0 16 16" aria-hidden="true"><path d="M3.5 1.5l2.5 0 1 3.5-1.6 1.2a9 9 0 0 0 4.4 4.4L11 9l3.5 1v2.5c0 1-.8 1.8-1.8 1.8C7.100 14.300 1.700 8.900 1.700 3.300c0-1 .8-1.8 1.800-1.800z"/></svg>
          <span>+001 555 210 4470</span>
        </li>
        <li class="contact__item">
          <svg class="contact__icon" viewBox="0 0 16 16" aria-hidden="true"><path d="M4 1h6l2 2v3H4zM2 7h12a1 1 0 0 1 1 1v6H1V8a1 1 0 0 1 1-1zm2 2v1h2V9zm3 0v1h2V9zm3 0v1h2V9zm-6 2v1h2v-1zm3 0v1h2v-1zm3 0v1h2v-1z"/></svg>
          <span>+001 555 210 4471</span>
        </li>
        <li class="contact__item">
          <svg class="contact__icon" viewBox="0 0 16 16" aria-hidden="true"><path d="M8 1a7 7 0 1 0 0 14A7 7 0 0 0 8 1zm0 1.5c.8 0 1.700 1.500 2 3.500H6c.3-2 1.200-3.500 2-3.500zM2.700 7h2.300a13 13 0 0 0 0 2H2.700a5.500 5.500 0 0 1 0-2zm3.300 0h4a12 12 0 0 1 0 2H6a12 12 0 0 1 0-2zm5 0h2.300a5.500 5.500 0 0 1 0 2H11a13 13 0 0 0 0-2zM6 10h4c-.3 2-1.200 3.500-2 3.500S6.300 12 6 10z"/></svg>
          <span>www.quarrowsignal.com</span>
        </li>
        <li class="contact__item">
          <svg class="contact__icon" viewBox="0 0 16 16" aria-hidden="true"><path d="M1 3h14v10H1zm1.500 1.300V5l5.500 4 5.500-4v-.7L8 8.300z"/></svg>
          <span>hello@quarrowsignal.com</span>
        </li>
      </ul>
    </div>

    <div class="brand">
      <span class="brand__dot" aria-hidden="true"></span>
      <p class="brand__name">Quarrow Signal<br>Instruments</p>
    </div>

    <div class="person">
      <p class="person__name">Marlene</p>
      <p class="person__role">Director</p>
    </div>
  </section>

  <section class="card card--back" aria-label="Business card back">
    <div class="brand brand--raised">
      <span class="brand__dot" aria-hidden="true"></span>
      <p class="brand__name">Quarrow Signal<br>Instruments</p>
    </div>
  </section>

</main>
</body>
</html>
```